Breakfast Cafe - The Sunny Nook

It is for my breakfast and lunch cafe with a hawaiian / beach theme. I am open 7 days a week from 7am to 2pm. We serve traditional American food such as omelettes, pancakes, burgers and sandwiches. I'll upload my old card and my new logo to be used. We have a lot of day to day regulars who eat there during the week, our t-shirts actually say 'Locals Only' on them. Hope this helps. Thanks.

Target Market(s)

anyone who has an appetite!

Industry/Entity Type

American Restaurant

Contact Information for Business Card

4815C Marlow Grove Avenue
Long Beach, California
(555) 731-2294

Requirements
Must have
• Address and phone number easily readable.
Nice to have
• beach or tropical theme

```html
<!DOCTYPE html>
<html lang="en">
<head>
<meta charset="utf-8">
<title>The Sunny Nook – Business Card</title>
<link href="https://fonts.googleapis.com/css2?family=Nunito+Sans:wght@600;700;800&display=swap" rel="stylesheet">
<style>
  :root {
    --page: #f5f5f5;
    --sky: #42a8ef;
    --cloud-far: #62b5f0;
    --cloud-near: #7dc4f4;
    --sand: #f7df9a;
    --sea: #4480c2;
    --badge-wood: #9a5a24;
    --badge-sun: #f6a94a;
    --name: #5bb8e0;
    --place: #a4562a;
    --white: #ffffff;
  }
  html, body {
    margin: 0;
    width: 1200px;
    height: 1200px;
    overflow: hidden;
    background: var(--page);
    font-family: "Nunito Sans", Arial, sans-serif;
  }
  .card {
    position: absolute;
    left: 261px;
    width: 677px;
    height: 386px;
    display: block;
  }
  .card--front { top: 131px; }
  .card--back { top: 648px; }
  .sky { fill: var(--sky); }
  .cloud-far { fill: var(--cloud-far); }
  .cloud-near { fill: var(--cloud-near); }
  .sand { fill: var(--sand); }
  .sea { fill: var(--sea); }
  .badge { fill: var(--badge-sun); stroke: var(--badge-wood); stroke-width: 20; }
  .brand-name { fill: var(--name); font-weight: 800; text-anchor: middle; }
  .brand-name--front { font-size: 46px; }
  .brand-name--back { font-size: 38px; }
  .brand-place { fill: var(--place); font-weight: 800; letter-spacing: 5px; text-anchor: middle; }
  .brand-place--front { font-size: 16px; }
  .brand-place--back { font-size: 14px; letter-spacing: 4px; }
  .contact { fill: var(--white); font-weight: 700; font-size: 21px; }
  .hours-title { fill: var(--white); font-weight: 700; font-size: 26px; letter-spacing: 1px; }
  .hours { fill: var(--white); font-weight: 700; font-size: 27px; }
  .icon-disc { fill: var(--white); }
  .icon-mark { fill: var(--cloud-near); }
</style>
</head>
<body>

<svg class="card card--front" viewBox="0 0 839 478" aria-label="Business card front">
  <rect class="sky" width="839" height="478"/>
  <path class="cloud-far" d="M0 72 Q60 60 135 88 Q170 20 240 40 Q290 -5 340 40 Q400 10 430 70 Q480 20 540 65 Q600 30 660 70 Q720 40 770 80 Q810 50 839 65 V478 H0 Z"/>
  <path class="cloud-near" d="M0 220 Q30 180 70 200 Q110 170 160 190 Q210 160 260 195 Q300 170 340 200 L500 200 Q560 150 620 195 Q660 140 720 170 Q780 130 839 210 V478 H0 Z"/>
  <path class="sand" d="M0 328 Q120 300 260 320 Q400 345 560 325 Q700 300 839 290 V478 H0 Z"/>
  <circle class="badge" cx="419" cy="193" r="135" role="img" aria-label="Badge illustration: beach scene with palm tree, sunrise, waves and ship"/>
  <text class="brand-name brand-name--front" x="419" y="366" textLength="336" lengthAdjust="spacingAndGlyphs">The Sunny Nook</text>
  <text class="brand-place brand-place--front" x="419" y="402">LONG BEACH, CA</text>
</svg>

<svg class="card card--back" viewBox="0 0 839 478" aria-label="Business card back">
  <rect class="sky" width="839" height="478"/>
  <path class="cloud-far" d="M0 72 Q60 60 135 88 Q170 20 240 40 Q290 -5 340 40 Q400 10 430 70 Q480 20 540 65 Q600 30 660 70 Q720 40 770 80 Q810 50 839 65 V478 H0 Z"/>
  <path class="cloud-near" d="M0 225 Q30 185 70 205 Q110 175 160 195 Q210 170 260 200 L340 200 Q390 150 440 180 Q500 150 560 200 Q620 150 690 190 Q760 150 839 225 V478 H0 Z"/>
  <path class="sea" d="M340 300 Q420 270 520 300 Q620 330 720 325 Q790 322 839 330 V478 H340 Z"/>
  <path class="sand" d="M0 270 Q150 262 290 280 Q380 292 400 330 Q460 400 618 478 H0 Z"/>
  <circle class="badge" cx="231" cy="204" r="115" role="img" aria-label="Badge illustration: beach scene with palm tree, sunrise, waves and ship"/>
  <text class="brand-name brand-name--back" x="231" y="350" textLength="286" lengthAdjust="spacingAndGlyphs">The Sunny Nook</text>
  <text class="brand-place brand-place--back" x="231" y="378">LONG BEACH, CA</text>

  <g class="icon-pin" transform="translate(429 161)">
    <circle class="icon-disc" r="15"/>
    <path class="icon-mark" d="M0 -9 a7 7 0 0 1 7 7 c0 5 -7 11 -7 11 c0 0 -7 -6 -7 -11 a7 7 0 0 1 7 -7 Z"/>
    <circle class="icon-disc" cy="-2" r="3"/>
  </g>
  <text class="contact" x="458" y="168">4815C Marlow Grove Avenue</text>
  <text class="contact" x="458" y="195">Long Beach, California</text>

  <g class="icon-phone" transform="translate(429 228)">
    <circle class="icon-disc" r="15"/>
    <path class="icon-mark" d="M-7 -8 l4 -1 l3 6 l-3 2 q2 5 7 7 l2 -3 l6 3 l-1 4 q-3 3 -8 1 q-9 -4 -12 -12 q-1 -4 2 -7 Z"/>
  </g>
  <text class="contact" x="458" y="235">(555) 731-2294</text>

  <text class="hours-title" x="414" y="290">BREAKFAST AND LUNCH</text>
  <text class="hours" x="414" y="326">7am-2pm daily</text>
</svg>

</body>
</html>
```